2018 Vision Board Workshop

I need to promote this workshop on both an 8.5x11 sheet and a 5x7 card. I do have a logo that needs to be present. I'd like to stay true to my branded colors. The flyer needs to project the excitement of a new year and the possibilities of what a person can create, produce, explore in their lives by putting it all on a vision board. Creating the vision of what you want will inspire you to achieve your goals and dreams. Looking at your vision board each day will propel you into taking action as you chart your course to achieve what you truly want.
The flyer needs to have the following information:
The workshop date and time - Sat., Jan. 13, 2018, 10:30-1:30
The location is - Studio 47B, 2486 Maple Ridge Ln, Colorado Springs, Co 80920
in the BUILD Room
My name and contact information - Mara Lindqvist
Text and voice 303-614-7752
Email - mara@bright-path-forward.com
Website - bright-path-forward.com
The fee is $45. All materials are provided.

My company is called Bright Path Forward. I am a Life Coach, author, speaker and workshop leader.\ I wrote this program, Bright Path Forward to teach concepts and supporting skills for living with more happiness, satisfaction and fulfillment. Thanks for reading this!! Mara

Target Market(s)

Primarily women, educated, motivated, proactive in their own lives and well being

Font styles to use
Other font styles liked:
• I have been using Century Gothic. I'm open to new ideas.

Requirements
Must have
• The Bright Path Forward logo
• The flyer needs to have the following information:
• The workshop date and time - Sat., Jan. 13, 2018, 10:30-1:30
• The location is - Studio 47B, 2486 Maple Ridge Ln, Colorado Springs, Co 80920
• in the BUILD Room
• My name and contact information - Mara Lindqvist
• Text and voice 303-614-7752
• Email - mara@bright-path-forward.com
• Website - bright-path-forward.com
• The fee is $45. All materials are provided.
Nice to have
• The Bright Path Forward branded colors in the design
• Images of vision boards

```html
<!DOCTYPE html>
<html lang="en">
<head>
<meta charset="utf-8">
<title>Bright Path Forward – Vision Board Workshop Flyer</title>
<link href="https://fonts.googleapis.com/css2?family=Questrial&family=Mulish:wght@400;600;700&display=swap" rel="stylesheet">
<style>
  :root {
    --brand-blue: #2f86c9;
    --brand-blue-light: #3aa6dc;
    --brand-blue-deep: #2a6fb8;
    --brand-green: #8cc63f;
    --lime: #86c52a;
    --ink-grey: #8a8a8a;
    --ink-dark: #666666;
    --board-top: #f2f7fc;
    --board-bottom: #dce9f6;
    --page-bg: #ececec;
    --pin: #4a4440;
    --white: #ffffff;
  }
  * { margin: 0; padding: 0; box-sizing: border-box; }
  html, body { width: 1200px; height: 1200px; overflow: hidden; background: var(--page-bg); }
  .canvas { position: relative; width: 1200px; height: 1200px; }
  .flyer {
    position: absolute; left: 151px; top: 20px;
    width: 1076px; height: 1392px;
    transform: scale(0.8333); transform-origin: 0 0;
    background: var(--white); overflow: hidden;
    font-family: "Questrial", sans-serif;
  }
  .abs { position: absolute; }
  .band { position: absolute; left: 0; width: 1076px; }
  .band-top { top: 0; height: 110px; }
  .band-bottom { bottom: 0; height: 240px; }

  .board {
    left: 41px; top: 112px; width: 1007px; height: 618px;
    background: linear-gradient(180deg, var(--board-top), var(--board-bottom));
    border-radius: 6px;
    box-shadow: 0 3px 8px rgba(0,0,0,0.25);
  }
  .pin { width: 14px; height: 14px; border-radius: 50%; background: var(--pin); box-shadow: 0 1px 2px rgba(0,0,0,0.5); }

  .photo { box-shadow: 0 3px 8px rgba(0,0,0,0.3); border: 4px solid var(--white); }
  .photo-cutout { left: 110px; top: 125px; width: 260px; height: 385px; border-radius: 120px 120px 10px 10px;
    background: linear-gradient(180deg, #e6d0bd, #a9dde0); }
  .photo-finance { left: 105px; top: 495px; width: 320px; height: 215px; transform: rotate(4deg);
    background: linear-gradient(135deg, #f4efe8, #c9cfc4); }
  .photo-relax { left: 375px; top: 340px; width: 210px; height: 215px; transform: rotate(-15deg);
    background: linear-gradient(180deg, #6fa9dc, #e9eef2); }
  .photo-shop { left: 510px; top: 450px; width: 250px; height: 255px; transform: rotate(-5deg);
    background: linear-gradient(160deg, #d3dcc8, #8e9a86); }
  .photo-family { left: 730px; top: 345px; width: 295px; height: 300px; transform: rotate(6deg);
    background: linear-gradient(180deg, #dbe9f3, #9fb8c6); }

  .brand-name { left: 420px; top: 225px; width: 620px; text-align: center;
    font-size: 60px; color: var(--lime); line-height: 1; }
  .brand-tagline { left: 420px; top: 294px; width: 620px; text-align: right; padding-right: 88px;
    font-size: 20px; letter-spacing: 1px; color: var(--brand-blue-light); }

  .title { left: 112px; width: 400px; font-size: 84px; line-height: 1; color: var(--brand-green); white-space: nowrap; }
  .title-vision { top: 778px; letter-spacing: 20px; }
  .title-board { top: 852px; letter-spacing: 20px; }
  .title-workshop { top: 928px; font-size: 66px; letter-spacing: 0; color: var(--brand-blue-deep); }
  .pitch { left: 120px; top: 1000px; width: 366px; text-align: right;
    font-size: 19px; line-height: 28px; letter-spacing: 3.4px; color: var(--ink-grey); }
  .pitch strong { font-weight: 400; color: var(--ink-dark); }

  .divider { left: 533px; top: 781px; width: 2px; height: 400px; background: var(--brand-blue-light); }

  .details { left: 568px; top: 816px; color: var(--brand-blue-light); }
  .day { font-size: 36px; letter-spacing: 4px; line-height: 44px; }
  .date { font-family: "Mulish", sans-serif; font-weight: 700; font-size: 37px; letter-spacing: 2px; line-height: 44px; color: var(--brand-blue); }
  .time { font-size: 36px; letter-spacing: 4.5px; line-height: 44px; }
  .venue { margin-top: 24px; font-size: 16px; letter-spacing: 3.5px; line-height: 25px; color: var(--ink-grey); text-transform: uppercase; }
  .fee { margin-top: 36px; font-size: 28px; letter-spacing: 2.5px; color: var(--brand-green); }
  .materials { margin-top: 12px; font-size: 20px; letter-spacing: 2.5px; color: var(--brand-green); }

  .contact { color: var(--white); font-family: "Mulish", sans-serif; text-transform: uppercase; white-space: nowrap; }
  .contact-name { left: 0; width: 1076px; top: 1278px; text-align: center; font-size: 32px; letter-spacing: 0.5px; }
  .contact-name b { font-weight: 700; }
  .link { top: 1332px; display: flex; align-items: center; gap: 18px; font-size: 24px; font-weight: 600; }
  .link-email { left: 52px; }
  .link-web { left: 603px; }
  .icon-tile { width: 44px; height: 44px; border-radius: 10px; background: var(--white); display: flex; align-items: center; justify-content: center; flex: none; }
</style>
</head>
<body>
<div class="canvas">
  <div class="flyer">
    <svg class="band band-top" viewBox="0 0 1076 110" preserveAspectRatio="none" aria-hidden="true">
      <defs>
        <linearGradient id="topBlue" x1="0" x2="1">
          <stop offset="0" stop-color="#2f86c9"/><stop offset="0.5" stop-color="#3aa6dc"/><stop offset="1" stop-color="#2a6fb8"/>
        </linearGradient>
      </defs>
      <path d="M0 0H1076V86Q538 20 0 86Z" fill="var(--brand-green)"/>
      <path d="M0 0H1076V74Q538 8 0 74Z" fill="url(#topBlue)"/>
      <path d="M0 104Q538 30 1076 86V84Q538 28 0 98Z" fill="var(--brand-green)"/>
    </svg>

    <div class="abs board"></div>
    <div class="abs pin" style="left:135px;top:99px"></div>
    <div class="abs pin" style="left:954px;top:99px"></div>
    <div class="abs pin" style="left:135px;top:725px"></div>
    <div class="abs pin" style="left:949px;top:725px"></div>

    <div class="abs photo-cutout" role="img" aria-label="Smiling woman in a light blue tank top giving a thumbs up with a tape measure at her waist"></div>
    <div class="abs photo photo-finance" role="img" aria-label="Hands counting cash beside a calculator and paperwork"></div>
    <div class="abs photo photo-relax" role="img" aria-label="Relaxed man stretching under a blue sky"></div>
    <div class="abs photo photo-shop" role="img" aria-label="Shop owner hanging an open sign in a doorway"></div>
    <div class="abs photo photo-family" role="img" aria-label="Family walking hand in hand along a seaside boardwalk"></div>

    <div class="abs brand-name">Bright Path Forward</div>
    <div class="abs brand-tagline">Picture it, then go and live it</div>

    <div class="abs title title-vision">VISION</div>
    <div class="abs title title-board">BOARD</div>
    <div class="abs title title-workshop">WORKSHOP</div>
    <p class="abs pitch">BE PART OF THE EXCITEMENT<br>OF A NEW YEAR AND THE<br>POSSIBILITIES OF WHAT YOU<br>CAN CREATE, PRODUCE,<br>EXPLORE IN YOUR LIVE<br>BY PUTTING IT ALL ON A<br><strong>VISION BOARD!</strong></p>

    <div class="abs divider"></div>

    <div class="abs details">
      <div class="day">SATURDAY</div>
      <div class="date">JANUARY 13, 2018</div>
      <div class="time">10:30 A.M - 1:30 P.M.</div>
      <div class="venue">Studio 47B, 2486 Maple Ridge Ln,<br>Colorado Springs, CO 80920<br>(at BUILD Room)</div>
      <div class="fee">WORKSHOP FEE $45</div>
      <div class="materials">ALL MATERIALS ARE PROVIDED</div>
    </div>

    <svg class="band band-bottom" viewBox="0 0 1076 240" preserveAspectRatio="none" aria-hidden="true">
      <defs>
        <linearGradient id="bottomBlue" x1="0" x2="1">
          <stop offset="0" stop-color="#2a6fb8"/><stop offset="0.5" stop-color="#3a9ad8"/><stop offset="1" stop-color="#2a6fb8"/>
        </linearGradient>
      </defs>
      <path d="M0 0Q538 150 1076 -6V2Q538 160 0 10Z" fill="var(--brand-green)"/>
      <path d="M0 20Q538 160 1076 10V240H0Z" fill="url(#bottomBlue)"/>
    </svg>

    <div class="abs contact contact-name"><b>Mara Lindqvist</b> Text and voice 303-614-7752</div>
    <div class="abs contact link link-email">
      <span class="icon-tile">
        <svg width="30" height="22" viewBox="0 0 30 22" aria-hidden="true"><rect x="1.5" y="1.5" width="27" height="19" rx="2" fill="none" stroke="var(--brand-blue)" stroke-width="2.5"/><path d="M2 3L15 13L28 3M2 19L11 10M28 19L19 10" fill="none" stroke="var(--brand-blue)" stroke-width="2.2"/></svg>
      </span>
      <span>mara@bright-path-forward.com</span>
    </div>
    <div class="abs contact link link-web">
      <span class="icon-tile">
        <svg width="30" height="30" viewBox="0 0 30 30" aria-hidden="true"><g fill="none" stroke="var(--brand-blue)" stroke-width="2"><circle cx="15" cy="15" r="12"/><ellipse cx="15" cy="15" rx="5.5" ry="12"/><path d="M3 15H27M5 9H25M5 21H25M15 3V27"/></g></svg>
      </span>
      <span>bright-path-forward.com</span>
    </div>
  </div>
</div>
</body>
</html>
```